Web Design Project

Desisgn a new style for the proposed website as per the attached link. The logo will remain as is, and it is likely that the colours will be as per the attached style guide.

Otherwise look and feel, icons, layout, images are within scope.

Current prosposed home page:
http://vantrelux-newsite.pagemorrowhost.com/index

Target Market(s)

Typically, large organisations from any industry such as Airlines, banks, Govt agencies.

Could be operational executives, business improvement specialists, bsuienss analysts.

```html
<!DOCTYPE html>
<html lang="en">
<head>
<meta charset="utf-8">
<title>Vantrelux — Operational Business Management</title>
<link href="https://fonts.googleapis.com/css2?family=Source+Sans+3:wght@400;600&display=swap" rel="stylesheet">
<style>
  :root {
    --navy-deep: #12204d;
    --navy-band: #2b4478;
    --navy-logo: #2e4a86;
    --heading-blue: #2b4478;
    --accent-orange: #e4561f;
    --text-body: #333333;
    --text-muted: #4a4a4a;
    --rule: #d6d6d6;
    --white: #ffffff;
  }
  * { margin: 0; padding: 0; box-sizing: border-box; }
  html, body { width: 1200px; height: 1142px; overflow: hidden; }
  body {
    position: relative;
    background: var(--white);
    font-family: "Source Sans 3", sans-serif;
    color: var(--text-body);
  }
  .abs { position: absolute; }

  .site-header { left: 0; top: 0; width: 1200px; height: 145px; background: var(--navy-deep); }
  .brand {
    left: 137px; top: 26px; width: 327px; height: 102px; background: var(--navy-logo);
    display: flex; align-items: center; justify-content: center; gap: 14px;
    color: var(--white); font-size: 38px; font-weight: 400; letter-spacing: 1px;
  }
  .brand-dot { width: 40px; height: 40px; border-radius: 50%; background: #5b86c8; }
  .search {
    left: 816px; top: 83px; width: 247px; height: 35px; border-radius: 8px;
    background: linear-gradient(#ffffff, #e9e9e9);
    font-size: 13px; color: #2b4478; padding: 9px 0 0 19px;
  }

  .main-nav { left: 0; top: 145px; width: 1200px; height: 39px; background: var(--navy-band); }
  .main-nav a {
    position: absolute; top: 0; height: 39px; line-height: 34px; text-align: center;
    color: var(--white); font-size: 12.5px; text-decoration: none;
    border-right: 1px solid #1a2d5a;
  }
  .main-nav a:last-child { border-right: 0; }

  .solution-list { left: 133px; top: 190px; width: 240px; }
  .solution {
    position: absolute; left: 0; width: 227px; display: flex; align-items: center;
    border-bottom: 1px solid var(--rule);
  }
  .solution:last-child { border-bottom: 0; }
  .solution-icon {
    width: 53px; height: 55px; border-radius: 4px; flex: none;
    border: 1px solid #d9d9d9; box-shadow: 1px 1px 2px #bbb;
    background: linear-gradient(#fafafa, #e6e6e6);
  }
  .solution-name { color: var(--accent-orange); font-size: 15.5px; line-height: 20px; white-space: nowrap; }

  .news-title { left: 138px; top: 667px; font-size: 18.5px; color: var(--navy-deep); }
  .news-item { left: 140px; width: 217px; }
  .news-item h3 { font-weight: 400; font-size: 14px; color: #111; margin-left: 1px; }
  .news-item p { font-size: 11.5px; line-height: 16px; text-align: justify; color: var(--text-muted); margin-top: 1px; }
  .news-item a { display: block; font-size: 11.5px; color: var(--heading-blue); text-decoration: none; margin-top: 9px; margin-left: 2px; }

  .hero { left: 383px; top: 206px; width: 685px; height: 356px; border: 1px solid #c8c8c8;
    background: radial-gradient(ellipse at 55% 70%, #6e7d95 0%, #b7c1cf 35%, #f3f4f6 70%, #ffffff 100%); }

  .welcome { left: 385px; top: 581px; font-size: 18px; color: var(--heading-blue); }
  .intro { left: 388px; top: 621px; width: 678px; font-size: 12.5px; line-height: 21px; text-align: justify; color: var(--text-body); }
  .divider { left: 390px; top: 789px; width: 677px; height: 1px; background: #c9c9c9; }

  .link-col h2 { font-weight: 400; font-size: 17.5px; color: var(--heading-blue); line-height: 20px; }
  .link-col ul { list-style: none; margin-top: 13px; }
  .link-col li { font-size: 11.5px; line-height: 24px; color: var(--text-muted); }

  .site-footer { left: 0; top: 1016px; width: 1200px; height: 126px; background: var(--navy-band); color: var(--white); text-align: center; }
  .footer-links { margin-top: 29px; font-size: 12.5px; word-spacing: 2px; }
  .footer-links span { margin: 0 6px; }
  .copyright { margin-top: 4px; font-size: 12.5px; }
</style>
</head>
<body>
  <header class="abs site-header"></header>
  <div class="abs brand"><span class="brand-dot"></span><span>vantrelux</span></div>
  <div class="abs search">Search</div>

  <nav class="abs main-nav">
    <a style="left:126px;width:130px">Products</a>
    <a style="left:256px;width:134px">Services</a>
    <a style="left:390px;width:134px">Solutions</a>
    <a style="left:524px;width:132px">Resources</a>
    <a style="left:656px;width:147px">Customer Stories</a>
    <a style="left:803px;width:129px">About Us</a>
    <a style="left:932px;width:140px">Contact Us</a>
  </nav>

  <div class="abs solution-list">
    <div class="solution" style="top:0;height:69px;"><span class="solution-icon" role="img" aria-label="Team icon" style="margin-left:19px"></span><span class="solution-name" style="margin-left:17px">Knowledge<br>Management</span></div>
    <div class="solution" style="top:69px;height:74px;"><span class="solution-icon" role="img" aria-label="Checklist with award icon" style="margin-left:19px"></span><span class="solution-name" style="margin-left:22px">Continuous<br>Improvement</span></div>
    <div class="solution" style="top:143px;height:78px;"><span class="solution-icon" role="img" aria-label="Document with data icon" style="margin-left:22px"></span><span class="solution-name" style="margin-left:23px">Business<br>Transformation</span></div>
    <div class="solution" style="top:221px;height:77px;"><span class="solution-icon" role="img" aria-label="Gears icon" style="margin-left:23px"></span><span class="solution-name" style="margin-left:15px">System Requirements</span></div>
    <div class="solution" style="top:298px;height:72px;"><span class="solution-icon" role="img" aria-label="Process flow icon" style="margin-left:23px"></span><span class="solution-name" style="margin-left:15px">Business Process<br>Modeling</span></div>
    <div class="solution" style="top:370px;height:72px;"><span class="solution-icon" role="img" aria-label="Governance building icon" style="margin-left:22px"></span><span class="solution-name" style="margin-left:16px">System<br>Requirements</span></div>
  </div>

  <h2 class="abs news-title" style="font-weight:400">News &amp; Events</h2>
  <div class="abs news-item" style="top:712px">
    <h3>SYDNEY</h3>
    <p>This unique way of reaching, engaging and empowering everyone involved in your business</p>
    <a>Read More &gt;&gt;</a>
  </div>
  <div class="abs news-item" style="top:832px">
    <h3>SYDNEY</h3>
    <p>This unique way of reaching, engaging and empowering everyone involved in your business</p>
    <a>Read More &gt;&gt;</a>
  </div>

  <div class="abs hero" role="img" aria-label="Photo of a group of five business professionals standing together"></div>

  <h1 class="abs welcome" style="font-weight:400">Welcome to Our Site</h1>
  <p class="abs intro">Operational excellence and business transformation is achieved by understanding and capturing every detail of your business. High performing companies have a single view of the complex relationships between systems, processes and people supported by in depth organizational knowledge. Vantrelux’s Operational Business Management System (OBMS) empowers and de-risks large transformation initiatives enabling continuous improvement for high performing organizations. An OBMS captures the DNA of your business. It links people, processes and systems in a way that visualizes how your organization works today, and how it may change in the future. This information is managed in a re-usable and extendable framework and is distributed to the many stakeholders in a form that meets their individual needs.</p>
  <div class="abs divider"></div>

  <section class="abs link-col" style="left:389px;top:817px">
    <h2>Products</h2>
    <ul style="margin-top:15px">
      <li>Modelvault</li><li>Vantrelux Modeler</li><li>- System Requirements Modeler</li>
      <li>- Performance Improvement Modeler</li><li>- Enterprise Architect Modeler</li><li>- Corporate Governance Modeler</li>
    </ul>
  </section>
  <section class="abs link-col" style="left:663px;top:817px">
    <h2>Services</h2>
    <ul><li>Coaching &amp; Mentoring</li><li>Technical Services</li></ul>
  </section>
  <section class="abs link-col" style="left:663px;top:913px">
    <h2>News &amp; Events</h2>
    <ul style="margin-top:6px"><li>Announcements</li><li>Technical Notes</li></ul>
  </section>
  <section class="abs link-col" style="left:907px;top:817px">
    <h2>Training Support</h2>
    <ul><li>Text-Based Tutorials</li><li>Tutorial Movies</li><li>Knowledge Base</li><li>Forums</li><li>Training Courses</li></ul>
  </section>

  <footer class="abs site-footer">
    <div class="footer-links">Products<span>|</span>Services<span>|</span>Solutions<span>|</span>Resources<span>|</span>Customer Stories<span>|</span>About Us<span>|</span>Contact Us</div>
    <div class="copyright">Copyrights @ 2012 All Rights Reserved</div>
  </footer>
</body>
</html>
```